Tolbek cards

I want a simple business card that pops.
Logo on one side.
On side two i want.
"Are you thinking about a new building on your property, or renovating an existing structure? Contact".....
Owners Name: Dale Whitacre
Owners Phone number: 610-555-0187
Address:4076 Copper Ridge RD, Elmhaven, PA 16999
Committed to Quality, Service, and Integrity

```html
<!DOCTYPE html>
<html lang="en">
<head>
<meta charset="utf-8">
<title>Tolbek Builders LLC – Business Cards</title>
<link href="https://fonts.googleapis.com/css2?family=Roboto:wght@400;700&family=Roboto+Condensed:wght@700&display=swap" rel="stylesheet">
<style>
  :root {
    --page-bg: #f0f0f0;
    --brown-dark: #412e1c;
    --brown-mid: #5a3920;
    --tan: #8f7860;
    --white: #ffffff;
    --text: #1f1a16;
  }
  * { box-sizing: border-box; margin: 0; padding: 0; }
  html, body {
    width: 1200px; height: 990px; overflow: hidden;
    background: var(--page-bg);
    font-family: "Roboto", Arial, sans-serif;
  }
  .canvas { position: relative; width: 1200px; height: 990px; }
  .card {
    position: absolute; left: 244px; width: 712px; height: 407px;
    border-radius: 46px; overflow: hidden;
    box-shadow: 0 14px 22px rgba(0,0,0,0.28);
  }
  /* Front */
  .card--front { top: 68px; background: var(--brown-dark); }
  .front-brand {
    position: absolute; inset: 0;
    display: flex; flex-direction: column; align-items: center; justify-content: center;
    color: var(--white); font-weight: 700; text-transform: uppercase;
    padding-top: 20px;
  }
  .front-brand__mark { width: 56px; height: 56px; background: var(--white); margin-bottom: 22px; }
  .front-brand__name { font-size: 84px; line-height: 0.9; letter-spacing: 1px; }
  .front-brand__sub { font-size: 27px; letter-spacing: 2px; margin-top: 8px; }

  /* Back */
  .card--back { top: 516px; background: var(--white); }
  .back-brand {
    position: absolute; left: 24px; top: 28px; width: 240px;
    display: flex; flex-direction: column; align-items: center;
    color: var(--brown-dark); font-weight: 700; text-transform: uppercase;
  }
  .back-brand__mark { width: 44px; height: 44px; background: var(--brown-dark); margin-bottom: 18px; }
  .back-brand__name { font-size: 58px; line-height: 0.9; }
  .back-brand__sub { font-size: 19px; letter-spacing: 1px; margin-top: 6px; }

  .owner { position: absolute; right: 28px; top: 22px; text-align: right; }
  .owner__name {
    font-family: "Roboto Condensed", "Arial Narrow", sans-serif;
    font-weight: 700; font-size: 44px; line-height: 1; color: var(--brown-dark);
  }
  .owner__role { font-size: 17px; color: var(--text); letter-spacing: 0.5px; margin-top: 2px; }

  .contact { position: absolute; right: 26px; top: 96px; text-align: right; font-size: 18.5px; color: var(--text); letter-spacing: 0.6px; line-height: 23px; }
  .contact__row { display: flex; justify-content: flex-end; align-items: flex-start; gap: 7px; }
  .contact__row svg { width: 17px; height: 17px; margin-top: 3px; flex: none; }
  .contact__text { display: block; }

  .pitch { position: absolute; left: 22px; top: 280px; font-size: 18.5px; line-height: 22.5px; color: var(--text); letter-spacing: 0.3px; }
  .tagline { position: absolute; right: 28px; top: 322px; font-size: 18.5px; line-height: 22.5px; color: var(--text); letter-spacing: 0.3px; }

  .bottom-band { position: absolute; left: 0; bottom: 0; width: 712px; height: 25px; }
</style>
</head>
<body>
<main class="canvas">
  <section class="card card--front" aria-label="Card front">
    <div class="front-brand">
      <div class="front-brand__mark"></div>
      <div class="front-brand__name">Tolbek</div>
      <div class="front-brand__sub">Builders LLC</div>
    </div>
  </section>

  <section class="card card--back" aria-label="Card back">
    <div class="back-brand">
      <div class="back-brand__mark"></div>
      <div class="back-brand__name">Tolbek</div>
      <div class="back-brand__sub">Builders LLC</div>
    </div>

    <div class="owner">
      <h1 class="owner__name">Dale Whitacre</h1>
      <p class="owner__role">Owners</p>
    </div>

    <div class="contact">
      <div class="contact__row">
        <span class="contact__text">610-555-0187</span>
        <svg viewBox="0 0 24 24" aria-hidden="true"><path fill="none" stroke="#412e1c" stroke-width="2.2" stroke-linejoin="round" d="M6 3l3 4-2 2c1 3 4 6 7 7l2-2 4 3-2 3c-7 0-14-7-15-15z"/><path fill="none" stroke="#412e1c" stroke-width="1.8" d="M14 3a7 7 0 0 1 7 7M14 7a3 3 0 0 1 3 3"/></svg>
      </div>
      <div class="contact__row">
        <span class="contact__text">4076 Copper Ridge RD, Elmhaven,<br>PA 16999</span>
        <svg viewBox="0 0 24 24" aria-hidden="true"><path fill="none" stroke="#412e1c" stroke-width="2.2" d="M12 22s-7-7-7-12a7 7 0 0 1 14 0c0 5-7 12-7 12z"/><circle cx="12" cy="10" r="3" fill="none" stroke="#412e1c" stroke-width="2"/></svg>
      </div>
    </div>

    <p class="pitch">"Are you thinking about a new<br>building on your property,<br>or renovating an existing<br>structure? Contact".....</p>
    <p class="tagline">Committed to Quality,<br>Service, and Integrity</p>

    <svg class="bottom-band" viewBox="0 0 712 25" preserveAspectRatio="none" aria-hidden="true">
      <defs>
        <linearGradient id="bandLeft" x1="0" x2="1">
          <stop offset="0" stop-color="#8f7860"/><stop offset="1" stop-color="#553720"/>
        </linearGradient>
        <linearGradient id="bandRight" x1="0" x2="1">
          <stop offset="0" stop-color="#553720"/><stop offset="1" stop-color="#8f7860"/>
        </linearGradient>
      </defs>
      <polygon points="0,0 364,0 334,25 0,25" fill="url(#bandLeft)"/>
      <polygon points="378,0 712,0 712,25 348,25" fill="url(#bandRight)"/>
    </svg>
  </section>
</main>
</body>
</html>
```